Quorimo Business Card Design Project

We need a business card design for quorimo.example a company based in Berlin, Germany.

?Quorimo is marketplace that enables people all over the world to monetize and exchange their individual knowledge and language skills through interactive video sessions. User are matched by their interests.

On Quorimo everybody can be student or teacher (seller or buyer).

We would love to see designs that use or main color blue and green. The design should communicate what Quorimo enables - see my notice above.

Looking so forward to your designs
Cheers from Berlin,
Lorenz

Target Market(s)

globally

Industry/Entity Type

Teacher

Requirements
Must have
• Lorenz Hubeck
CEO
Quorimo.example

Quorimo e-Services GmbH
Lindenweg 87
10247 Berlin

Fon: +49 30 418 906 25 17
Mobile: 49 172 54 91 37 6
E-Mail: l.hubeck@quorimo.example
Web: www.quorimo.example

```html
<!DOCTYPE html>
<html lang="en">
<head>
<meta charset="utf-8">
<title>Quorimo Business Cards</title>
<link href="https://fonts.googleapis.com/css2?family=Questrial&family=Arimo:wght@700&display=swap" rel="stylesheet">
<style>
  :root {
    --blue: #1ea3dc;
    --grey: #6a6a6a;
    --ink: #3a3a3a;
    --rule: #bdbdbd;
    --card: #ffffff;
    --backdrop: #e6e7e9;
  }
  * { margin: 0; padding: 0; box-sizing: border-box; }
  html, body { width: 954px; height: 1200px; overflow: hidden; }
  body {
    background: var(--backdrop);
    position: relative;
    font-family: "Questrial", Arial, sans-serif;
    color: var(--ink);
  }
  .card {
    position: absolute;
    left: 76px;
    width: 800px;
    height: 456px;
    background: var(--card);
    border-radius: 24px;
    box-shadow: 0 4px 14px rgba(0,0,0,0.18);
    text-align: center;
  }
  .card--front { top: 83px; }
  .card--back { top: 642px; }

  .company-name {
    position: absolute; left: 0; right: 0;
    font-family: "Questrial", Arial, sans-serif;
    color: var(--grey);
    line-height: 1;
  }
  .card--front .company-name { top: 70px; font-size: 76px; }

  .person {
    position: absolute; top: 208px; left: 0; right: 0;
    font-size: 19px; color: var(--ink);
  }
  .person__name {
    font-family: "Arimo", Arial, sans-serif;
    font-weight: 700; font-size: 30px; color: var(--blue);
  }
  .person__sep { margin: 0 8px; }

  .contacts {
    position: absolute; top: 277px; left: 0; right: 0;
    display: flex; justify-content: center;
    font-size: 20px; line-height: 26px;
  }
  .contacts__col { padding: 0 14px; text-align: left; }
  .contacts__col + .contacts__col { border-left: 1px solid var(--rule); }
  .contact { display: flex; align-items: center; gap: 8px; white-space: nowrap; }
  .contact svg { width: 18px; height: 18px; flex: none; }

  .address {
    position: absolute; top: 366px; left: 0; right: 0;
    font-size: 20px; line-height: 26px;
  }

  .card--back .company-name { top: 240px; font-size: 72px; }
  .web {
    position: absolute; top: 345px; left: 0; right: 0;
    font-family: "Arimo", Arial, sans-serif; font-weight: 700;
    font-size: 30px; color: var(--blue);
  }
</style>
</head>
<body>
  <section class="card card--front">
    <div class="company-name">Quorimo</div>

    <div class="person">
      <span class="person__name">Lorenz Hubeck</span><span class="person__sep">I</span>CEO
    </div>

    <div class="contacts">
      <div class="contacts__col">
        <div class="contact">
          <svg viewBox="0 0 18 18" aria-hidden="true"><path fill="var(--blue)" d="M2 7c0-3 14-3 14 0v1h-3V6.5C11 5.8 7 5.8 5 6.5V8H2zM4 9h10l1 6H3z"/></svg>
          +49 30 418 906 25 17
        </div>
        <div class="contact">
          <svg viewBox="0 0 18 18" aria-hidden="true"><rect x="5" y="2" width="8" height="15" rx="1.5" fill="var(--blue)"/><rect x="6.5" y="4" width="5" height="4" fill="#fff"/></svg>
          49 172 54 91 37 6
        </div>
      </div>
      <div class="contacts__col">
        <div class="contact">
          <svg viewBox="0 0 18 18" aria-hidden="true"><rect x="2" y="4" width="14" height="11" rx="1" fill="none" stroke="var(--blue)" stroke-width="1.5"/><path d="M2.5 5l6.5 5 6.5-5" fill="none" stroke="var(--blue)" stroke-width="1.5"/></svg>
          l.hubeck@quorimo.example
        </div>
        <div class="contact">
          <svg viewBox="0 0 18 18" aria-hidden="true"><circle cx="9" cy="9" r="7" fill="var(--blue)"/><path d="M2 9h14M9 2c-3 3-3 11 0 14M9 2c3 3 3 11 0 14" fill="none" stroke="#fff" stroke-width="1"/></svg>
          www.quorimo.example
        </div>
      </div>
    </div>

    <div class="address">
      Quorimo e-Services GmbH, Lindenweg 87<br>10247 Berlin
    </div>
  </section>

  <section class="card card--back">
    <div class="company-name">Quorimo</div>
    <div class="web">www.quorimo.example</div>
  </section>
</body>
</html>
```